Copper Lantern

Need a business card for our restaurant. Restaurant and Bar in the mountains of North Idaho. Rustic looking card

rustic design, wood and metal looking, primarily neutral colors

• Name, address, phone number, website, email address

```html
<!DOCTYPE html>
<html lang="en">
<head>
<meta charset="utf-8">
<title>Copper Lantern – Business Card</title>
<link href="https://fonts.googleapis.com/css2?family=Lato:wght@400;700&family=Permanent+Marker&display=swap" rel="stylesheet">
<style>
  :root {
    --page-bg: #2b2b2b;
    --card-dark: #0d0d0d;
    --card-mid: #2a2a2a;
    --ink: #f2f2f2;
    --ink-soft: #d6d6d6;
    --rule: #bdbdbd;
  }
  * { box-sizing: border-box; margin: 0; padding: 0; }
  html, body { width: 1200px; height: 875px; overflow: hidden; }
  body {
    background: var(--page-bg);
    display: flex;
    flex-direction: column;
    align-items: center;
    justify-content: center;
    gap: 44px;
    font-family: "Lato", sans-serif;
    color: var(--ink);
  }
  .card {
    position: relative;
    width: 640px;
    height: 366px;
    border-radius: 18px;
    overflow: hidden;
  }
  .card-texture {
    position: absolute;
    inset: 0;
    background:
      radial-gradient(ellipse at 65% 35%, rgba(90,90,90,0.55), transparent 55%),
      radial-gradient(ellipse at 25% 70%, rgba(60,60,60,0.4), transparent 50%),
      linear-gradient(135deg, var(--card-mid), var(--card-dark) 70%);
  }

  /* Front */
  .front-brand {
    position: absolute;
    inset: 0;
    display: flex;
    align-items: center;
    justify-content: center;
    gap: 16px;
  }
  .brand-dot {
    width: 14px; height: 14px;
    border-radius: 50%;
    background: var(--ink);
  }
  .brand-name {
    font-family: "Lato", sans-serif;
    font-weight: 700;
    font-size: 40px;
    letter-spacing: 3px;
    text-transform: uppercase;
    color: var(--ink);
  }

  /* Back */
  .back-mark {
    position: absolute;
    top: 26px;
    right: 30px;
    font-weight: 700;
    font-size: 15px;
    letter-spacing: 2px;
    text-transform: uppercase;
    color: var(--ink);
  }
  .back-content {
    position: absolute;
    left: 0; right: 0;
    top: 150px;
    display: flex;
    align-items: center;
    justify-content: flex-end;
    padding-right: 40px;
  }
  .person {
    text-align: right;
    padding-right: 22px;
  }
  .person-name {
    font-family: "Permanent Marker", cursive;
    font-size: 32px;
    letter-spacing: 1px;
    color: var(--ink-soft);
    line-height: 1.1;
  }
  .person-role {
    font-size: 15px;
    color: var(--ink-soft);
    margin-top: 2px;
  }
  .divider {
    width: 1px;
    height: 112px;
    background: var(--rule);
  }
  .contact-list {
    list-style: none;
    padding-left: 20px;
    display: flex;
    flex-direction: column;
    gap: 7px;
  }
  .contact-item {
    display: flex;
    align-items: center;
    gap: 9px;
    font-size: 14px;
    color: var(--ink-soft);
  }
  .contact-icon { width: 12px; height: 12px; flex: none; }
</style>
</head>
<body>

  <section class="card card-front">
    <div class="card-texture" role="img" aria-label="Dark weathered chalkboard texture"></div>
    <div class="front-brand">
      <span class="brand-dot"></span>
      <span class="brand-name">Copper Lantern</span>
    </div>
  </section>

  <section class="card card-back">
    <div class="card-texture" role="img" aria-label="Dark weathered chalkboard texture"></div>
    <div class="back-mark">Copper Lantern</div>
    <div class="back-content">
      <div class="person">
        <div class="person-name">MARCUS HALE</div>
        <div class="person-role">Founder &amp; CEO</div>
      </div>
      <div class="divider"></div>
      <ul class="contact-list">
        <li class="contact-item">
          <svg class="contact-icon" viewBox="0 0 24 24"><path fill="#d6d6d6" d="M6.6 10.8a15 15 0 0 0 6.6 6.6l2.2-2.2c.3-.3.7-.4 1-.2 1.1.4 2.3.6 3.6.6.6 0 1 .4 1 1V20c0 .6-.4 1-1 1A17 17 0 0 1 3 4c0-.6.4-1 1-1h3.5c.6 0 1 .4 1 1 0 1.3.2 2.5.6 3.6.1.3 0 .7-.2 1z"/></svg>
          (208) 555-0147
        </li>
        <li class="contact-item">
          <svg class="contact-icon" viewBox="0 0 24 24"><rect x="2" y="5" width="20" height="14" rx="2" fill="#d6d6d6"/><path d="M3 6l9 7 9-7" stroke="#111" stroke-width="2" fill="none"/></svg>
          info@copperlanternridge.com
        </li>
        <li class="contact-item">
          <svg class="contact-icon" viewBox="0 0 24 24"><circle cx="12" cy="12" r="9" fill="none" stroke="#d6d6d6" stroke-width="2"/><path d="M3 12h18M12 3c3 3 3 15 0 18M12 3c-3 3-3 15 0 18" fill="none" stroke="#d6d6d6" stroke-width="1.6"/></svg>
          copperlanternridge.com
        </li>
        <li class="contact-item">
          <svg class="contact-icon" viewBox="0 0 24 24"><path fill="#d6d6d6" d="M12 2a7 7 0 0 0-7 7c0 5 7 13 7 13s7-8 7-13a7 7 0 0 0-7-7zm0 9.5A2.5 2.5 0 1 1 12 6.5a2.5 2.5 0 0 1 0 5z"/></svg>
          48 Pine Hollow Rd, Ridgefield, ID 83800
        </li>
      </ul>
    </div>
  </section>

</body>
</html>
```